Rebranding of WordPress website | Velmar and Co

We currently have a wordpress website www.tordelbrewhouse.com.au that we need rebranded to Velmar and Co and modernised. Velmar and Co is an import export business. The website is also linked to Shopify.The current website was created as a coffee website but will now need to have the main page then have the 3 product pages of a menu. Our New web address is www.velmarandco.com.au Our general Enquiries email is enquiries@velmarandco.com.au and we are also on Facebook and Instagram. We are looking for a clean fresh looking website, not too fussy. Black, white, natural textures.

```html
<!DOCTYPE html>
<html lang="en">
<head>
<meta charset="utf-8">
<title>Velmar &amp; Co</title>
<link rel="stylesheet" href="https://fonts.googleapis.com/css2?family=Oswald:wght@300;400;500&family=Mulish:wght@400;600;700&display=swap">
<style>
:root{
  --ink:#111111;
  --white:#ffffff;
  --muted:#6b6b6b;
  --rule:#d8d8d8;
  --sand:#efe3d3;
  --sand-deep:#e4d3bd;
  --hero-a:#1d1a18;
  --hero-b:#4a3d33;
  --vip-a:#151515;
  --vip-b:#2e2a27;
}
*{margin:0;padding:0;box-sizing:border-box}
html,body{width:1200px;height:2976px;overflow:hidden}
body{position:relative;background:var(--white);color:var(--ink);font-family:"Mulish",sans-serif}
.abs{position:absolute}
.heading{font-family:"Oswald",sans-serif;font-weight:300;letter-spacing:2px;text-transform:uppercase}

/* header */
.site-header{left:0;top:0;width:1200px;height:160px;background:var(--white)}
.brand{left:112px;top:48px;display:flex;align-items:center;gap:16px}
.brand-square{width:56px;height:56px;background:var(--ink)}
.brand-name{font-family:"Oswald",sans-serif;font-weight:500;font-size:34px;letter-spacing:2px;color:var(--ink);text-transform:uppercase}
.header-icons{left:930px;top:28px;display:flex;gap:14px}
.icon-circle{width:42px;height:42px;border:2px solid var(--ink);border-radius:50%;display:flex;align-items:center;justify-content:center}
.main-nav{left:565px;top:106px;display:flex;gap:44px;font-family:"Oswald",sans-serif;font-size:15px;letter-spacing:1px;text-transform:uppercase}

/* hero */
.hero{left:0;top:160px;width:1200px;height:620px;background:linear-gradient(160deg,var(--hero-a) 0%,var(--hero-b) 45%,#2a231f 70%,var(--hero-a) 100%);color:var(--white);text-align:center}
.hero-title{position:absolute;left:0;width:1200px;top:118px;font-size:56px;line-height:70px;font-weight:400;letter-spacing:4px}
.hero-sub{position:absolute;left:300px;width:600px;top:210px;font-size:26px;line-height:36px}
.hero-btn{position:absolute;left:515px;top:420px;width:170px;height:56px;border:2px solid var(--white);border-radius:6px;font-size:20px;line-height:52px;background:rgba(0,0,0,.25)}
.slide-arrow{position:absolute;top:294px;width:30px;height:30px;border-radius:50%;background:rgba(255,255,255,.85);display:flex;align-items:center;justify-content:center}

/* welcome */
.welcome{left:0;top:780px;width:1200px;height:400px;background:var(--white);text-align:center}
.cup-art{position:absolute;left:880px;top:40px;width:200px;height:160px;background:radial-gradient(ellipse at center,#ededed 0%,rgba(255,255,255,0) 70%)}
.section-title{position:absolute;left:0;width:1200px;font-size:46px;line-height:56px;text-align:center}
.title-rule{position:absolute;left:520px;width:160px;height:2px;background:var(--ink)}
.welcome-text{position:absolute;left:300px;width:600px;top:166px;font-size:14px;line-height:22px;color:var(--muted);text-align:center}
.outline-btn{position:absolute;border:1.5px solid var(--ink);border-radius:30px;font-size:16px;letter-spacing:1px;text-transform:uppercase;text-align:center}

/* products */
.products{left:0;top:1180px;width:1200px;height:575px;background:linear-gradient(180deg,var(--sand) 0%,var(--sand-deep) 100%)}
.card{position:absolute;top:160px;width:210px;height:380px;background:var(--white);text-align:center;box-shadow:0 2px 8px rgba(0,0,0,.08)}
.card-img{width:150px;height:150px;border-radius:50%;margin:24px auto 22px;background:radial-gradient(circle at 40% 40%,#5a3a26 0%,#2a1a12 70%)}
.card-brand{font-size:12px;font-weight:700;letter-spacing:1px;text-transform:uppercase}
.card-name{font-size:19px;margin-top:8px}
.card-price{font-size:22px;font-weight:700;margin-top:6px}
.card-btn{width:110px;height:38px;margin:18px auto 0;border:1px solid var(--rule);font-size:14px;line-height:36px}
.prod-arrow{position:absolute;top:310px}

/* feature */
.feature{left:0;top:1755px;width:1200px;height:555px;background:var(--white)}
.machine-art{position:absolute;left:170px;top:175px;width:390px;height:330px;background:linear-gradient(135deg,#d6d6d6 0%,#8e8e8e 50%,#3b3b3b 100%);border-radius:12px}
.bag-art{position:absolute;left:930px;top:250px;width:200px;height:220px;background:radial-gradient(ellipse at center,#eeeeee 0%,rgba(255,255,255,0) 70%)}
.feature-info{position:absolute;left:595px;top:95px;width:380px}
.feature-name{font-size:30px;font-weight:700}
.feature-maker{font-size:14px;color:var(--muted);margin-top:8px}
.feature-price{font-size:24px;margin-top:20px}
.feature-price small{font-size:15px;color:var(--muted)}
.feature-desc{font-size:13px;line-height:20px;color:var(--muted);margin-top:16px}
.feature-free{font-size:15px;font-weight:700;margin-top:16px}
.select{width:350px;height:40px;border:1px solid var(--rule);margin-top:14px;padding:0 14px;font-size:14px;line-height:38px;display:flex;justify-content:space-between}
.dark-btn{width:120px;height:44px;background:var(--ink);color:var(--white);font-size:15px;line-height:44px;text-align:center;margin-top:20px}

/* vip */
.vip{left:0;top:2310px;width:1200px;height:350px;background:linear-gradient(180deg,var(--vip-a),var(--vip-b));color:var(--white);text-align:center}
.vip-title{position:absolute;left:0;width:1200px;top:70px;font-size:48px;line-height:60px;font-weight:400}
.vip-sub{position:absolute;left:0;width:1200px;top:140px;font-size:18px}
.vip-input{position:absolute;left:260px;top:200px;width:560px;height:52px;background:var(--white);color:#777;text-align:left;padding-left:18px;font-size:15px;line-height:52px}
.vip-submit{position:absolute;left:820px;top:200px;width:120px;height:52px;background:#000;color:var(--white);font-size:15px;line-height:52px;letter-spacing:1px}

/* footer */
.site-footer{left:0;top:2660px;width:1200px;height:316px;background:var(--white);text-align:center}
.footer-brand{position:absolute;left:0;width:1200px;top:80px;display:flex;justify-content:center;align-items:center;gap:16px}
.footer-nav{position:absolute;left:0;width:1200px;top:238px;display:flex;justify-content:center;gap:26px;font-family:"Oswald",sans-serif;font-size:15px;text-transform:uppercase;letter-spacing:1px}
.footer-nav span.sep{color:#999}
.copyright{position:absolute;left:0;width:1200px;top:272px;font-size:14px;color:var(--muted)}
</style>
</head>
<body>

<header class="site-header abs">
  <div class="brand abs"><span class="brand-square"></span><span class="brand-name">Velmar &amp; Co</span></div>
  <div class="header-icons abs">
    <span class="icon-circle"><svg width="18" height="18" viewBox="0 0 18 18"><circle cx="7.5" cy="7.5" r="5" fill="none" stroke="#111" stroke-width="2"/><line x1="11" y1="11" x2="16" y2="16" stroke="#111" stroke-width="2"/></svg></span>
    <span class="icon-circle"><svg width="18" height="18" viewBox="0 0 18 18"><circle cx="9" cy="6" r="3.5" fill="none" stroke="#111" stroke-width="2"/><path d="M2 17c0-4 3-6 7-6s7 2 7 6" fill="none" stroke="#111" stroke-width="2"/></svg></span>
    <span class="icon-circle"><svg width="18" height="18" viewBox="0 0 18 18"><path d="M1 2h3l2 10h9l2-7H5" fill="none" stroke="#111" stroke-width="2"/><circle cx="7" cy="15.5" r="1.5" fill="#111"/><circle cx="14" cy="15.5" r="1.5" fill="#111"/></svg></span>
  </div>
  <nav class="main-nav abs"><span>Home</span><span>Products</span><span>Guaranteed Me Support</span><span>VIP Club</span><span>Contact Us</span></nav>
</header>

<section class="hero abs" role="img" aria-label="Dim café photograph of an espresso machine pouring coffee">
  <div class="slide-arrow" style="left:16px"><svg width="14" height="14" viewBox="0 0 14 14"><path d="M9 2L4 7l5 5" fill="none" stroke="#111" stroke-width="2"/></svg></div>
  <div class="slide-arrow" style="left:1154px"><svg width="14" height="14" viewBox="0 0 14 14"><path d="M5 2l5 5-5 5" fill="none" stroke="#111" stroke-width="2"/></svg></div>
  <h1 class="hero-title heading">Velmar &amp; Co</h1>
  <p class="hero-sub">Take in the beauty of Italy through artisan Velmar &amp; co sed ut perspiciatis unde omnis iste</p>
  <div class="hero-btn">Shop Now!</div>
</section>

<section class="welcome abs">
  <div class="cup-art" role="img" aria-label="Faint sketch of a coffee cup and beans"></div>
  <h2 class="section-title heading" style="top:82px">Welcome to Velmar &amp; Co</h2>
  <div class="title-rule" style="top:148px"></div>
  <p class="welcome-text">We bring the finest Italian coffee and espresso gear straight to your door. Every blend is roasted in small batches, packed fresh and shipped with care so each cup at home tastes just like a morning at a corner café in Venice. Explore our range and find a favourite that suits your daily ritual.</p>
  <div class="outline-btn" style="left:540px;top:314px;width:120px;height:44px;line-height:41px">Read More</div>
</section>

<section class="products abs" role="group" aria-label="Coffee products">
  <h2 class="section-title heading" style="top:56px">Coffee Products</h2>
  <div class="title-rule" style="top:122px"></div>
  <svg class="prod-arrow" style="left:56px" width="24" height="90" viewBox="0 0 24 90"><path d="M20 2L4 45l16 43" fill="none" stroke="#333" stroke-width="2"/></svg>
  <svg class="prod-arrow" style="left:1120px" width="24" height="90" viewBox="0 0 24 90"><path d="M4 2l16 43L4 88" fill="none" stroke="#333" stroke-width="2"/></svg>

  <div class="card" style="left:150px"><div class="card-img" role="img" aria-label="Bag of espresso beans"></div><div class="card-brand">Serrano Nero</div><div class="card-name">Caffe Serrano</div><div class="card-price">$30.00</div><div class="card-btn">Add to Cart</div></div>
  <div class="card" style="left:390px"><div class="card-img" role="img" aria-label="Tin of ground coffee"></div><div class="card-brand">Caffe Lidova</div><div class="card-name">Caffe Serrano</div><div class="card-price">$30.00</div><div class="card-btn">Add to Cart</div></div>
  <div class="card" style="left:630px"><div class="card-img" role="img" aria-label="Bag of espresso beans"></div><div class="card-brand">Serrano Nero</div><div class="card-name">Caffe Serrano</div><div class="card-price">$30.00</div><div class="card-btn">Add to Cart</div></div>
  <div class="card" style="left:870px"><div class="card-img" role="img" aria-label="Pack of coffee pods"></div><div class="card-brand">Serrano Nero</div><div class="card-name">Caffe Serrano</div><div class="card-price">$30.00</div><div class="card-btn">Add to Cart</div></div>
</section>

<section class="feature abs">
  <div class="machine-art" role="img" aria-label="Stainless steel espresso machine"></div>
  <div class="bag-art" role="img" aria-label="Faint sketch of a coffee sack"></div>
  <div class="feature-info">
    <div class="feature-name">The Crema Classic</div>
    <div class="feature-maker">Aldorne</div>
    <div class="feature-price">$762.29 $899.00 <small>Rrp</small></div>
    <p class="feature-desc">Create great tasting espresso in less than a minute with this all-in-one machine. Grind, dose and extract with precise temperature control for café quality results at home.</p>
    <div class="feature-free">FREE 1 x 1kg bag of Italian Espresso Coffee</div>
    <div class="select"><span>Choose</span><svg width="12" height="38" viewBox="0 0 12 38"><path d="M2 16l4 5 4-5" fill="none" stroke="#555" stroke-width="1.5"/></svg></div>
    <div class="dark-btn">Add To Cart</div>
  </div>
</section>

<section class="vip abs" role="img" aria-label="Dark café background photograph">
  <h2 class="vip-title heading">Join Our VIP Club</h2>
  <p class="vip-sub">Join to receive discounts and earn exclusive rewards</p>
  <div class="vip-input">Enter Email Id</div>
  <div class="vip-submit">SUBMIT</div>
</section>

<footer class="site-footer abs">
  <div class="footer-brand"><span class="brand-square"></span><span class="brand-name">Velmar &amp; Co</span></div>
  <nav class="footer-nav"><span>Home</span><span class="sep">|</span><span>Products</span><span class="sep">|</span><span>Guaranteed Me Support</span><span class="sep">|</span><span>VIP Club</span><span class="sep">|</span><span>Contact Us</span></nav>
  <p class="copyright">© Copyright 2019 Velmar &amp; Co. All rights reserved.</p>
</footer>

</body>
</html>
```